The Linen Loft Co

We need a business card design for our wardrobe company.
Please visit our website www.gentlelinenlofts.com to get an idea of who we are.

```html
<!DOCTYPE html>
<html lang="en">
<head>
<meta charset="utf-8">
<title>The Linen Loft Co – Business Card</title>
<link href="https://fonts.googleapis.com/css2?family=Open+Sans:wght@400;600;700&display=swap" rel="stylesheet">
<style>
  :root {
    --bg-light: #eef0f2;
    --bg-dark: #c9ccd0;
    --card-dark: #2b2a28;
    --card-white: #ffffff;
    --ink: #1f1f1f;
    --ink-soft: #3a3a3a;
    --gold: #8c7551;
    --wood: #7a5f44;
    --wood-light: #b89c7c;
    --slate: #4a4b4f;
  }
  * { box-sizing: border-box; margin: 0; padding: 0; }
  html, body { width: 1200px; height: 800px; overflow: hidden; }
  body {
    background: radial-gradient(ellipse at 60% 35%, var(--bg-light), var(--bg-dark));
    font-family: "Open Sans", Arial, sans-serif;
    position: relative;
  }
  .card {
    position: absolute;
    top: 245px;
    width: 540px;
    height: 310px;
    overflow: hidden;
    box-shadow: 0 10px 24px rgba(0,0,0,0.22);
  }
  /* Front */
  .card--front { left: 40px; background: var(--card-dark); }
  .brand {
    position: absolute;
    display: flex;
    align-items: center;
    gap: 14px;
  }
  .brand__mark { width: 22px; height: 22px; }
  .brand__name {
    font-weight: 600;
    font-size: 15px;
    letter-spacing: 2px;
    text-transform: uppercase;
  }
  .brand__tagline {
    font-size: 13px;
    font-weight: 600;
    letter-spacing: 0.6px;
    margin-top: 3px;
  }
  .card--front .brand { left: 150px; top: 40px; color: #8e8c88; }
  .card--front .brand__mark { background: #5a5855; }
  .gallery {
    position: absolute;
    left: 0; right: 0;
    top: 118px;
    height: 124px;
    display: flex;
    gap: 5px;
  }
  .gallery__photo { flex: 1; }
  .gallery__photo--warm { background: linear-gradient(160deg, var(--wood-light), var(--wood) 60%, #3a2f25); }
  .gallery__photo--dark { background: linear-gradient(180deg, #3c3d41, var(--slate) 50%, #8d8e92); }
  .gallery__photo--lit { background: linear-gradient(150deg, #e4d5bf, #b79d7d 55%, #6d5a47); }

  /* Back */
  .card--back { left: 620px; background: var(--card-white); }
  .card--back .brand { left: 34px; top: 40px; color: var(--ink); }
  .card--back .brand__mark { background: var(--ink); }
  .rule {
    position: absolute;
    left: 34px; right: 34px;
    top: 150px;
    height: 1px;
    background: var(--gold);
  }
  .contact {
    position: absolute;
    left: 34px;
    top: 168px;
    list-style: none;
    font-size: 13px;
    color: var(--ink-soft);
    line-height: 22px;
  }
  .contact li { display: flex; align-items: center; gap: 8px; }
  .contact svg { width: 12px; height: 12px; flex: none; }
  .person {
    position: absolute;
    right: 34px;
    top: 164px;
    text-align: right;
  }
  .person__name { color: var(--gold); font-weight: 700; font-size: 19px; }
  .person__role { font-size: 13px; color: var(--ink-soft); margin-top: 1px; }
  .address {
    position: absolute;
    right: 34px;
    top: 218px;
    text-align: right;
    font-size: 13px;
    line-height: 18px;
    color: var(--ink-soft);
    font-style: normal;
  }
  .footer-band {
    position: absolute;
    left: 0; bottom: 0;
    width: 540px; height: 14px;
  }
</style>
</head>
<body>

<section class="card card--front" aria-label="Card front">
  <div class="brand">
    <span class="brand__mark" aria-hidden="true"></span>
    <div>
      <div class="brand__name">The Linen Loft Co</div>
      <div class="brand__tagline">Calm Spaces, Kept in Order</div>
    </div>
  </div>
  <div class="gallery">
    <div class="gallery__photo gallery__photo--warm" role="img" aria-label="Walk-in wardrobe with wooden shelving and hanging clothes"></div>
    <div class="gallery__photo gallery__photo--dark" role="img" aria-label="Dark dressing room with a round ottoman in the centre"></div>
    <div class="gallery__photo gallery__photo--lit" role="img" aria-label="Illuminated wardrobe units with glass fronts"></div>
  </div>
</section>

<section class="card card--back" aria-label="Card back">
  <div class="brand">
    <span class="brand__mark" aria-hidden="true"></span>
    <div>
      <div class="brand__name">The Linen Loft Co</div>
      <div class="brand__tagline">Calm Spaces, Kept in Order</div>
    </div>
  </div>

  <div class="rule"></div>

  <ul class="contact">
    <li>
      <svg viewBox="0 0 12 12" aria-hidden="true"><path d="M2.5 1 L4.5 1 L5 3.5 L3.8 4.5 Q5 7 7.5 8.2 L8.5 7 L11 7.5 L11 9.5 Q10.5 11 9 11 Q1 10 1 3 Q1 1.5 2.5 1 Z" fill="#8c7551"/></svg>
      0207 555 0148
    </li>
    <li>
      <svg viewBox="0 0 12 12" aria-hidden="true"><rect x="0.75" y="2.25" width="10.5" height="7.5" fill="none" stroke="#8c7551" stroke-width="1.2"/><path d="M0.75 2.25 L6 6.5 L11.25 2.25" fill="none" stroke="#8c7551" stroke-width="1.2"/></svg>
      mara@gentlelinenlofts.com
    </li>
    <li>
      <svg viewBox="0 0 12 12" aria-hidden="true"><circle cx="6" cy="6" r="5" fill="none" stroke="#8c7551" stroke-width="1.1"/><ellipse cx="6" cy="6" rx="2.2" ry="5" fill="none" stroke="#8c7551" stroke-width="1"/><path d="M1 6 H11 M2 3.5 H10 M2 8.5 H10" stroke="#8c7551" stroke-width="0.9"/></svg>
      www.gentlelinenlofts.com
    </li>
  </ul>

  <div class="person">
    <div class="person__name">Mara Lindqvist</div>
    <div class="person__role">Design Consultant &amp; Dream Maker</div>
  </div>

  <address class="address">
    Hollis House<br>
    42 Harbour Lane<br>
    London N1 4QT
  </address>

  <svg class="footer-band" viewBox="0 0 540 14" preserveAspectRatio="none" aria-hidden="true">
    <polygon points="0,0 300,0 312,14 0,14" fill="#2b2a28"/>
    <polygon points="306,4 540,4 540,14 314,14" fill="#8c7551"/>
  </svg>
</section>

</body>
</html>
```